Business Card for my New Brokerage

Looking to get a business card design for my new Real Estate Brokerage.
I want it with Picture, Phone Number, Email, Website, Office Address
Name and Designation. Please add logo too.

Target Market(s)

Real Estate Investors or Home Buyers

Industry/Entity Type

Real Estate

Contact Information for Business Card

Name, Email, Phone Number, website, email, office address

Colors
EB3D1F
EC4F4E
F09395
F8D3D4
FCEDEE

Requirements
Must have
• Minimalistic, Clean, Modern, Photo
Nice to have
• White and Red Colors

```html
<!DOCTYPE html>
<html lang="en">
<head>
<meta charset="utf-8">
<title>Ember Realty Inc — Business Card</title>
<link href="https://fonts.googleapis.com/css2?family=Montserrat:wght@400;500;700;800&display=swap" rel="stylesheet">
<style>
  :root {
    --backdrop: #1b1b1b;
    --brand-red: #dd0000;
    --card-white: #ffffff;
    --ink-grey: #4a4a4a;
    --silver: #c4c2c2;
    --photo-light: #dfe6ee;
    --photo-navy: #2a3144;
  }
  * { box-sizing: border-box; margin: 0; padding: 0; }
  html, body {
    width: 1200px; height: 1199px; overflow: hidden;
    background: var(--backdrop);
    font-family: "Montserrat", sans-serif;
  }
  .card {
    position: absolute; left: 195px; width: 800px; height: 436px;
    box-shadow: 0 18px 30px rgba(0,0,0,.55);
  }
  .card-front { top: 115px; background: var(--card-white); }
  .card-back { top: 650px; background: var(--brand-red); }

  .portrait {
    position: absolute; left: 71px; top: 63px; width: 288px; height: 318px;
    border: 2px solid var(--brand-red); border-radius: 24px;
    background: linear-gradient(180deg, var(--photo-light) 0%, #c9d3df 55%, var(--photo-navy) 100%);
  }

  .details { position: absolute; left: 439px; top: 60px; color: var(--ink-grey); }
  .brand-name {
    color: var(--brand-red); font-weight: 800; text-transform: uppercase;
    line-height: 1; text-align: center; width: 292px;
  }
  .brand-name .line-main { display: block; font-size: 58px; letter-spacing: 1px; }
  .brand-name .line-sub { display: block; font-size: 19px; letter-spacing: 5px; margin-top: 8px; }

  .person-name {
    margin-top: 30px; color: var(--brand-red); font-weight: 700;
    font-size: 31px; letter-spacing: 1px; line-height: 1;
  }
  .person-title { margin-top: 6px; font-size: 19px; line-height: 1.2; }
  .address { margin-top: 12px; font-size: 19px; line-height: 26px; }
  .contact-list { list-style: none; margin-top: 10px; font-size: 19px; line-height: 27px; }
  .contact-list li { display: flex; align-items: center; gap: 8px; }
  .contact-list svg { width: 14px; height: 14px; flex: none; }

  .back-brand {
    position: absolute; left: 0; right: 0; top: 165px; text-align: center;
    color: var(--silver); font-weight: 800; text-transform: uppercase; line-height: 1;
  }
  .back-brand .line-main { display: block; font-size: 118px; letter-spacing: 2px; }
  .back-brand .line-sub { display: block; font-size: 32px; letter-spacing: 9px; margin-top: 14px; font-weight: 800; }
</style>
</head>
<body>
  <section class="card card-front">
    <div class="portrait" role="img" aria-label="Headshot portrait of the agent in a navy blazer"></div>
    <div class="details">
      <div class="brand-name">
        <span class="line-main">Ember</span>
        <span class="line-sub">Realty Inc</span>
      </div>
      <h1 class="person-name">DANIEL HART</h1>
      <p class="person-title">Founder and President</p>
      <p class="address">1820 Cedar Hollow Lane<br>Macon Springs, GA 31210</p>
      <ul class="contact-list">
        <li>
          <svg viewBox="0 0 24 24"><path fill="#dd0000" d="M6.6 10.8a15.5 15.5 0 0 0 6.6 6.6l2.2-2.2a1 1 0 0 1 1-.25 11.4 11.4 0 0 0 3.6.57 1 1 0 0 1 1 1V20a1 1 0 0 1-1 1A17 17 0 0 1 3 4a1 1 0 0 1 1-1h3.5a1 1 0 0 1 1 1c0 1.25.2 2.45.57 3.57a1 1 0 0 1-.25 1z"/></svg>
          +330 5550-1427
        </li>
        <li>
          <svg viewBox="0 0 24 24"><rect x="2" y="5" width="20" height="14" rx="2" fill="none" stroke="#dd0000" stroke-width="2.4"/><path d="M3 6l9 7 9-7" fill="none" stroke="#dd0000" stroke-width="2.4"/></svg>
          info@emberrealtyinc.com
        </li>
        <li>
          <svg viewBox="0 0 24 24"><g fill="none" stroke="#dd0000" stroke-width="2"><circle cx="12" cy="12" r="10"/><ellipse cx="12" cy="12" rx="4.5" ry="10"/><path d="M2 12h20M4 7h16M4 17h16"/></g></svg>
          www.emberrealtyinc.com
        </li>
      </ul>
    </div>
  </section>

  <section class="card card-back">
    <div class="back-brand">
      <span class="line-main">Ember</span>
      <span class="line-sub">Realty Inc</span>
    </div>
  </section>
</body>
</html>
```